PYLON SIGN FOR “MEADOWLARK CAR WASH SPRINT”

please see the new images in my brief. I have a logo design and the colors I would like you to follow.

please put "meadowlark car wash sprint" in the logo

Target Market(s)

GENERAL PUBLIC

Industry/Entity Type

CAR WASH

Font styles to use
Other font styles liked:
• CURSIVE AND BLOCK LETTERING BOTH AS IN THE SAMPLE PIC

Colors
00AB8E
00BBA5
67D7C9
C6EFE9
E9F9F6
6B429C
8869AF
B7A5CE
E3DAEB
F3F0F8

Requirements
Must have
• 1. “MEADOWLARK CAR WASH SPRINT” PLEASE PUT THIS IN THE LOGO 2. USE BLACK, WHITE, GREEN AND SILVER FOR A COLOR
Nice to have
• I WOULD LIKE TO SEE THE SIGN IN BOTH COLOR THEMES: WHITE, BLACK, GREEN AND SILVER AND WHITE BLACK PURPLE AND SILVER

```html
<!DOCTYPE html>
<html lang="en">
<head>
<meta charset="utf-8">
<title>Meadowlark Car Wash Sprint – Pylon Sign</title>
<link rel="stylesheet" href="https://fonts.googleapis.com/css2?family=Michroma&family=Russo+One&display=swap">
<style>
  :root {
    --page: #e6e6e6;
    --sign-black: #050505;
    --foam-light: #3a3a3a;
    --foam-dark: #0b0b0b;
    --band-green: #1e3f06;
    --lime: #a4d80f;
    --lime-shadow: #0d1c03;
    --silver-light: #ffffff;
    --silver-mid: #c9c9c9;
    --silver-dark: #8f8f8f;
  }
  * { margin: 0; padding: 0; box-sizing: border-box; }
  html, body {
    width: 830px;
    height: 1200px;
    overflow: hidden;
    background: var(--page);
  }
  .sign {
    position: absolute;
    left: 30px;
    top: 306px;
    width: 770px;
    height: 588px;
    background: var(--sign-black);
    overflow: hidden;
    box-shadow: 0 4px 14px rgba(0,0,0,0.25);
  }
  .sign-shapes {
    position: absolute;
    inset: 0;
    width: 770px;
    height: 588px;
  }
  .brand-lockup {
    position: absolute;
    left: 0;
    right: 0;
    top: 118px;
    display: flex;
    align-items: center;
    justify-content: center;
    gap: 12px;
  }
  .brand-dot {
    width: 14px;
    height: 14px;
    border-radius: 50%;
    background: var(--lime);
  }
  .brand-name {
    font-family: "Michroma", sans-serif;
    font-size: 19px;
    line-height: 1.45;
    color: var(--lime);
    text-align: center;
    letter-spacing: 1px;
  }
  .headline {
    position: absolute;
    left: 0;
    right: 0;
    top: 262px;
    text-align: center;
  }
  .silver {
    display: block;
    font-family: "Michroma", sans-serif;
    background: linear-gradient(180deg, var(--silver-light) 0%, var(--silver-mid) 55%, var(--silver-dark) 100%);
    -webkit-background-clip: text;
    background-clip: text;
    color: transparent;
  }
  .headline-top {
    font-size: 29px;
    letter-spacing: 2px;
    line-height: 44px;
  }
  .headline-main {
    display: block;
    font-family: "Russo One", sans-serif;
    font-size: 108px;
    line-height: 104px;
    color: var(--lime);
    letter-spacing: 1px;
    text-shadow: 5px 4px 0 var(--lime-shadow);
    transform: skewX(-4deg);
  }
  .headline-bottom {
    font-size: 48px;
    letter-spacing: 3px;
    line-height: 64px;
  }
</style>
</head>
<body>
  <main class="sign">
    <svg class="sign-shapes" viewBox="0 0 770 588" xmlns="http://www.w3.org/2000/svg">
      <defs>
        <radialGradient id="foamTone" cx="0.3" cy="0.2" r="0.9">
          <stop offset="0" stop-color="var(--foam-light)"/>
          <stop offset="0.6" stop-color="var(--foam-dark)"/>
          <stop offset="1" stop-color="#000"/>
        </radialGradient>
      </defs>
      <rect class="foam-backdrop" x="0" y="0" width="770" height="250" fill="url(#foamTone)" role="img" aria-label="Photograph of dark soap foam bubbles"/>
      <polygon class="torn-black-layer" fill="#000"
        points="0,232 30,226 62,230 95,222 130,228 170,221 210,226 250,220 290,227 330,222 370,228 410,221 450,226 490,220 530,227 570,222 610,229 650,221 690,227 730,222 770,228 770,588 0,588"/>
      <polygon class="green-band" fill="var(--band-green)"
        points="0,262 24,254 48,259 80,248 112,255 140,246 175,252 205,244 240,250 270,243 305,249 338,241 372,247 400,240 432,246 465,241 498,248 530,242 560,249 595,243 625,251 660,245 690,252 722,247 750,254 770,250
                770,530 745,524 720,529 690,518 660,524 632,516 600,522 570,513 540,520 508,512 478,518 448,510 418,516 390,509 360,515 330,508 300,515 270,510 240,518 210,512 180,520 150,514 120,521 90,516 60,524 30,518 0,523"/>
    </svg>

    <div class="brand-lockup">
      <span class="brand-dot"></span>
      <p class="brand-name">MEADOWLARK<br>CAR WASH SPRINT</p>
    </div>

    <h1 class="headline">
      <span class="silver headline-top">MEADOWLARK</span>
      <span class="headline-main">CAR WASH</span>
      <span class="silver headline-bottom">SPRINT</span>
    </h1>
  </main>
</body>
</html>
```